Flyer-Design für Karla Brettin
Zielgruppe
Ich bin psychologische Beraterin und Heilpraktikerin für Psychotherapie. Ich biete ein Coaching speziell für Mütter (meist Mütter mit neugeborenen Babys) an. Dieses Mütter-Coaching will ich bewerben. Die Flyer werden unter anderen an Ärzte und Hebammen weiter gegeben und dort in den Praxen ausliegen.
Aufgabenstellung
In meinem Logo herrschen die Farben orange und grau vor - es wäre schön, wenn sich diese Farben im Flyer wiederfinden würden - evtl. kombiniert mit mittelblau oder einem hellem grün.
Des weiteren möchte ich später Flyer im Din Lang Format (einseitig) mit anderen Angeboten erstellen. Das sollte mit dem Design dann auch möglich sein.
Der Schrifttyp soll bitte Arial sein, passend zum Logo. Ich habe bei Bildarro Fotos zu dem Thema erstanden, die ich stimmig finde. Diese Bilder sollten im Flyer genutzt werden.
Für diesen Flyer hätte ich gerne das Format: Falzblatt mit Wickelfalz - 279 x 219 mm

```html
<!DOCTYPE html>
<html lang="de">
<head>
<meta charset="utf-8">
<title>Coaching für Mütter – Falzblatt</title>
<link href="https://fonts.googleapis.com/css2?family=Arimo:ital,wght@0,400;0,700;1,400&display=swap" rel="stylesheet">
<style>
:root{
  --orange:#e0962e;
  --grey:#7b7b7b;
  --grey-dark:#5f5f5f;
  --ink:#111;
  --paper:#fff;
  --stage:#c9c9cb;
  --photo-a:#b9a9a0;
  --photo-b:#6f7488;
  --note:#8a8a8a;
}
*{box-sizing:border-box;margin:0;padding:0}
html,body{width:1200px;height:1200px;overflow:hidden}
body{background:linear-gradient(180deg,#f4f4f5 0%,var(--stage) 100%);font-family:"Arimo",Arial,sans-serif;color:var(--grey);position:relative}
.sheet{position:absolute;background:var(--paper);border:1px solid #222}
.sheet--outer{left:53px;top:20px;width:824px;height:583px}
.sheet--inner{left:342px;top:602px;width:820px;height:580px}
.col{position:absolute;font-size:9.6px;line-height:13.6px}
.just{text-align:justify;hyphens:manual}
.center{text-align:center}
.accent{color:var(--orange)}
.strong{font-weight:700}
.wordmark{font-size:17px;font-weight:400;color:var(--orange);letter-spacing:.2px;display:flex;align-items:center;justify-content:center;gap:5px}
.wordmark .dot{width:8px;height:8px;border-radius:50%;background:var(--orange)}
.brand-title{font-size:13.5px;font-weight:700;color:var(--grey-dark);margin-top:6px}
.brand-sub{font-size:10.5px;color:var(--grey-dark);margin-top:3px}
.photo{position:absolute;background:linear-gradient(135deg,var(--photo-a),#d9cfc8 45%,var(--photo-b))}
p+p{margin-top:13.6px}
.offer+.offer{margin-top:13.6px}
.offer b{color:var(--orange)}
.sec-head{font-size:13.8px;font-weight:700;color:var(--grey-dark);text-align:center;letter-spacing:.6px}
.bullets{list-style:none;margin-top:22px}
.bullets li{position:relative;padding-left:14px;text-align:justify}
.bullets li+li{margin-top:13.6px}
.bullets li::before{content:"";position:absolute;left:0;top:4px;width:5px;height:5px;border-radius:50%;background:var(--orange)}
.sub{font-weight:700;text-align:center;color:var(--grey-dark)}
.note{background:var(--note);color:#fff;font-size:8.4px;line-height:13.6px;padding:1px 4px;text-align:justify}
</style>
</head>
<body>

<section class="sheet sheet--outer" aria-label="Außenseite">
  <div class="col" style="left:28px;top:26px;width:214px">
    <h2 class="center" style="font-size:11.6px;color:var(--grey-dark)">Warum Coaching extra für Mütter?</h2>
    <p class="center" style="margin-top:13px;font-size:9.6px">Nun:</p>
    <p class="center" style="margin-top:13px;font-size:11.2px;font-style:italic">Nur wer gut für sich selbst sorgt,<br>kann auch für andere da sein!</p>
    <h2 class="center" style="margin-top:45px;font-size:13.6px;color:var(--grey-dark)">Coaching <span class="accent">für Mütter</span></h2>
    <div class="just" style="margin-top:36px">
      <p>Als Heilpraktikerin für Psychotherapie und ge­prüfte psychologische Beraterin habe ich mich besonders auf das Coaching für Mütter spezia­lisiert.</p>
      <p>Ich setzte dabei die Methode des lösungsorien­tierten Kurzzeitcoachings ein, das den <span style="color:var(--ink)">Fokus auf Stärken und Lösungen</span> legt und nicht die Probleme und Hindernisse in den Vordergrund stellt.</p>
      <p>Das Konzept wird durch Achtsamkeits- und Ent­spannungsübungen abgerundet. Aspekte der „gewaltfreien“ = wertschätzenden Kommunika­tion werden für individuelle Konfliktlösungen im familiären Alltag genutzt.</p>
      <p class="strong" style="color:var(--ink);margin-top:26px;text-align:left">Starten Sie mit einem neuen und liebevollen Blick auf Ihr Leben und auf Ihre Fähigkeiten.</p>
      <p>Sie werden erstaunt sein, was alles in Ihnen wohnt</p>
    </div>
  </div>

  <div class="col" style="left:297px;top:30px;width:222px">
    <div class="center">
      <div class="wordmark"><span class="dot"></span>karlabrettin</div>
      <div class="brand-title">Coaching für Mütter</div>
      <div class="brand-sub">Begleitung – Stärkung – Beratung</div>
    </div>
    <div class="just" style="margin-top:38px">
      <p class="offer"><b>Einzelcoaching</b> Sie können wählen: das Coa­ching kann in meiner Praxis in Lindenfeld oder gern auch bei Ihnen zu Hause stattfinden, allein oder mit Partner, so wie es gerade für Sie am bes­ten passt.</p>
      <p class="offer"><b>Gruppencoaching</b> Lernen Sie Gleichgesinnte kennen und profitieren Sie in doppelter Hinsicht – nach dem Motto: <i>„Lieber gemeinsam als einsam“</i>.</p>
      <p class="offer"><b>TelefonCoaching</b> Sie bestimmen Ort und Zeit. Dieses Angebot könnte das Richtige für Sie sein, wenn Sie zeitlich oder örtlich gebunden sind.</p>
    </div>
    <div class="center" style="margin-top:46px">
      <p>Rufen Sie mich doch einfach unverbindlich an<br>- ich freue mich auf Sie!</p>
      <p class="strong" style="font-size:11.6px;color:var(--grey-dark);margin-top:17px">Karla Brettin</p>
      <p style="margin-top:13px;line-height:13px">Heilpraktikerin für Psychotherapie<br>Geprüfte Psychologische Beraterin</p>
      <p style="margin-top:13px;line-height:13px">Telefon: 0160 482 16 305<br>Email: info@karla-brettin.de<br>Homepage: www.karla-brettin.de</p>
      <p style="margin-top:13px;line-height:13px">Praxisgemeinschaft am Hain<br>Dachsweg 14b<br>40991 Lindenfeld am Rhein</p>
    </div>
  </div>

  <div class="photo" role="img" aria-label="Foto: erschöpfte Mutter hält ihr schlafendes Baby im Arm" style="left:546px;top:0;width:277px;height:292px"></div>
  <div class="col center" style="left:546px;top:330px;width:277px">
    <p style="font-size:18px;line-height:25.5px;color:var(--grey)">Das Baby ist da<br>und nichts ist mehr<br>wie es war</p>
    <div style="margin-top:64px">
      <div class="wordmark"><span class="dot"></span>karlabrettin</div>
      <div class="brand-title">Coaching für Mütter</div>
      <div class="brand-sub">Begleitung – Stärkung – Beratung</div>
    </div>
  </div>
</section>

<section class="sheet sheet--inner" aria-label="Innenseite">
  <div class="photo" role="img" aria-label="Fotostreifen: Mutter mit Baby, in hellen senkrechten Bahnen verblassend, rechts lächelnde Mutter mit schlafendem Baby an der Schulter" style="left:0;top:0;width:818px;height:120px;background:linear-gradient(90deg,#8f8580 0%,#7a7f92 17%,#e3e1e4 28%,#dcd9dc 55%,#cbc8cc 72%,#e6e4e6 80%,#a99a92 90%,#ececee 100%)"></div>

  <div class="col" style="left:28px;top:138px;width:220px">
    <h3 class="sec-head"><span class="accent">Ihre</span> <span class="accent">Situation</span></h3>
    <ul class="bullets">
      <li>Haben Sie sich Ihr Mutterglück anders vorge­stellt? - Sie hatten sich so auf Ihr Baby gefreut, aber die Realität ist gar nicht so, wie Sie sie sich das gedacht haben?</li>
      <li>Oder Sie haben bereits ein oder mehrere Kinder aber trotzdem ist jetzt alles anders?</li>
      <li>Fühlen Sie sich allein, isoliert: Ihre Kollegen und Freunde führen weiterhin Ihr früheres Leben – Sie sind aber nicht mehr mit dabei?</li>
      <li>Das Verständnis Ihrer Umgebung für Ihre neue Situation fehlt. Sogar die Partnerschaft ist plötzlich ganz anders als sie es vorher war?</li>
      <li>Sie werden nur noch als Mutter wahrgenom­men – kaum mehr als die Frau und die Persönlichkeit, die Sie vorher waren und auch immer noch sind?</li>
      <li>Sie fühlen sich oft erschöpft, ratlos, überfor­dert, unverstanden?</li>
    </ul>
  </div>

  <div class="col just" style="left:304px;top:138px;width:220px">
    <h3 class="sec-head"><span class="accent">Meine</span> Unterstützung</h3>
    <p class="sub" style="margin-top:13px">Begleitung</p>
    <p style="margin-top:0">Die gute Nachricht: Sie müssen diese belastende Situation nicht allein bewältigen - erleben Sie Er­leichterung, indem Sie sich von mir beraten lassen.</p>
    <p style="margin-top:9px">Als Coach gehe ich ganz individuell auf Ihre Person und auf Ihre persönliche Situation ein.</p>
    <p class="sub" style="margin-top:11px">Stärkung</p>
    <p style="margin-top:0">Entscheiden Sie sich für einen Weg, der zu Ihnen passt und Sie glücklich macht.</p>
    <p>Finden Sie die Mutterrolle, die es Ihnen ermöglicht, gut für sich zu sorgen und bei sich zu bleiben. Le­ben Sie so Ihre Bedürfnisse und Interessen im Ein­klang mit denen Ihrer Familie.</p>
    <p class="sub" style="margin-top:24px">Beratung</p>
    <p style="margin-top:0">Trotz einer Flut an Informationen fühlen sich viele Mütter mit ihren Themen alleine gelassen, hilflos und überfordert.</p>
    <p>Bei mir bleiben Sie nicht allein und ratlos: zusam­men finden wir individuelle Antworten auf Ihre ganz persönlichen Fragen.</p>
  </div>

  <div class="col" style="left:579px;top:138px;width:213px">
    <h3 class="sec-head"><span class="accent">Unser</span> Weg</h3>
    <p class="just" style="margin-top:22px">Gemeinsam können wir uns Ihre Themen an­sehen und bearbeiten:</p>
    <ul class="bullets" style="margin-top:13.6px">
      <li>Stressbewältigung – finden Sie den Weg zu mehr Gelassenheit, zur inneren Ruhe</li>
      <li>Zeiteinteilung – so passen Sie Ihre Zeit der momentanen Situation an</li>
      <li>Erhalten Sie mehr Klarheit über Ihre Bedürf­nisse und Erwartungen</li>
      <li>Wandeln Sie Unsicherheit in Stabilität um</li>
      <li>Erkennen und nutzen Sie Ihre Stärken und Fähigkeiten</li>
      <li>Familienberatung – so können Sie entgegen kommend miteinander umgehen</li>
      <li>Netzwerk – hier finden Sie Verständnis und Unterstützung</li>
    </ul>
    <p class="note" style="margin-top:26px">Hinweis: Es handelt sich hier um eine Beratung und nicht um eine Psychotherapie oder sonstige Heilkunde im gesetzlichen Sinne und soll diese auch nicht ersetzen.</p>
  </div>
</section>

</body>
</html>
```